Business card design

I already have the logo design completed and am requiring business card design and layout utilising the logo. I require a front and back design.

We are an executive recruitment company so we are looking at full colour, high finish in a reasonably conservative structure.

Reason: will be provide ai template

Target Market(s)

Senior Management 35-60 age bracket

Industry/Entity Type

Business

Requirements
Must have
• Peter Welling
• Director
• 238 Morrow Tce, Kelvin Grove QLD 4059
• Ph: 07 3628 4190 Mob: 0418527306
• peter@voltinapartners.com.au
• www.voltinapartners.com.au
Nice to have
• Ideally full colour,
Should not have
• cheap looking

```html
<!DOCTYPE html>
<html lang="en">
<head>
<meta charset="utf-8">
<title>Voltina Partners – Business Cards</title>
<link rel="stylesheet" href="https://fonts.googleapis.com/css2?family=Open+Sans:wght@300;400;700&display=swap">
<style>
  :root {
    --backdrop: #3a2f3c;
    --navy-deep: #0b2a5a;
    --navy: #1a4c8e;
    --brand-blue: #1d4a86;
    --paper: #ffffff;
    --ink-grey: #9a9a9a;
    --title-grey: #a8a8a8;
    --on-navy: #ffffff;
  }
  * { margin: 0; padding: 0; box-sizing: border-box; }
  html, body {
    width: 1200px;
    height: 800px;
    overflow: hidden;
    background: var(--backdrop);
    font-family: "Open Sans", Arial, sans-serif;
  }
  .stage {
    position: relative;
    width: 1200px;
    height: 800px;
    display: flex;
    align-items: center;
    justify-content: center;
    gap: 60px;
  }
  .card {
    position: relative;
    width: 525px;
    height: 300px;
    border-radius: 4px;
    overflow: hidden;
    box-shadow: 0 14px 30px rgba(0, 0, 0, 0.35);
  }

  /* Back of card */
  .card--back {
    background: radial-gradient(ellipse at 40% 35%, var(--navy) 0%, var(--navy-deep) 85%);
    color: var(--on-navy);
  }
  .card--back .brand {
    position: absolute;
    left: 0; right: 0;
    top: 112px;
    justify-content: center;
  }
  .card--back .brand-mark { background: var(--on-navy); }
  .card--back .brand-name { color: var(--on-navy); }
  .website {
    position: absolute;
    left: 0; right: 0;
    top: 196px;
    text-align: center;
    font-size: 17px;
    font-weight: 400;
    letter-spacing: 0.5px;
  }

  /* Front of card */
  .card--front {
    background: var(--paper);
  }
  .edge-band {
    position: absolute;
    top: 0; right: 0;
    width: 8px;
    height: 100%;
    background: var(--brand-blue);
  }
  .card--front .brand {
    position: absolute;
    left: 40px;
    top: 38px;
  }
  .card--front .brand-mark { background: var(--brand-blue); }
  .card--front .brand-name { color: var(--brand-blue); }

  .brand {
    display: flex;
    align-items: center;
    gap: 14px;
  }
  .brand-mark {
    width: 34px;
    height: 34px;
  }
  .brand-name {
    font-weight: 700;
    font-size: 26px;
    letter-spacing: 2px;
    line-height: 1;
  }

  .person {
    position: absolute;
    left: 40px;
    top: 100px;
  }
  .person-name {
    font-size: 19px;
    font-weight: 700;
    color: var(--brand-blue);
  }
  .person-title {
    font-size: 14px;
    font-weight: 400;
    color: var(--title-grey);
    margin-top: 1px;
  }

  .contact {
    position: absolute;
    right: 40px;
    bottom: 28px;
    list-style: none;
    font-size: 13px;
    font-weight: 300;
    line-height: 1.5;
    color: var(--ink-grey);
  }
</style>
</head>
<body>
  <main class="stage">
    <section class="card card--back" aria-label="Card back">
      <div class="brand">
        <span class="brand-mark"></span>
        <span class="brand-name">VOLTINA PARTNERS</span>
      </div>
      <p class="website">www.voltinapartners.com.au</p>
    </section>

    <section class="card card--front" aria-label="Card front">
      <div class="brand">
        <span class="brand-mark"></span>
        <span class="brand-name">VOLTINA PARTNERS</span>
      </div>
      <div class="person">
        <h1 class="person-name">Peter Welling</h1>
        <p class="person-title">Director</p>
      </div>
      <ul class="contact">
        <li>238 Morrow Tce, Kelvin Grove</li>
        <li>QLD 4059</li>
        <li>P: 07 3628 4190</li>
        <li>M: 0418 527 306</li>
        <li>peter@voltinapartners.com.au</li>
      </ul>
      <span class="edge-band"></span>
    </section>
  </main>
</body>
</html>
```